Create a Big Data Website that is professional but has a creative flare to it.

I am after a modern business design for a company in the Big Data space however it still needs to have a wow value and something stand out from other corporate websites.
My competitors websites are to give you and idea of content:
www.tarnvilla.com
www.pluvoria.com
www.meridu4.com.au
www.quornaby.com
I have uploaded my company Logo so you can use that to make sure it matches your theme.

Target Market(s)

Banks, Insurance Companies, Government, Gas and Energy Companies and Food Manufacturing.

Industry/Entity Type

Consulting

Coding

Number of Pages Required

5+ page

Colors

Designer to choose colors to be used in the design.

Requirements
Must have
• Images, Diagrams around Big Data. Usage of information or graphs from sources like Velsham are fine to use.
Nice to have
• Interactive design use mouse overs, change in text, highlighting information for clear focus.
Should not have
• Cluttered Pages of Informaiton

```html
<!DOCTYPE html>
<html lang="en">
<head>
<meta charset="utf-8">
<title>Calderwen Consulting</title>
<link href="https://fonts.googleapis.com/css2?family=Poppins:ital,wght@0,400;0,500;0,600;0,700;1,400&display=swap" rel="stylesheet">
<style>
:root{
  --navy:#1b3a6b;
  --blue:#0b6cb8;
  --blue-deep:#0a4d8f;
  --blue-bright:#1587d6;
  --ink:#333a44;
  --muted:#5b6470;
  --italic:#5e7aa6;
  --panel:#e9ebee;
  --hex:#8a8d92;
  --footer:#1f2124;
  --footer-line:#3a3d42;
  --white:#ffffff;
}
*{box-sizing:border-box;margin:0;padding:0}
html,body{width:1200px;height:4063px;overflow:hidden}
body{font-family:"Poppins",sans-serif;color:var(--ink);background:var(--white);position:relative}
.abs{position:absolute}
.section-title{font-weight:600;text-transform:uppercase;color:var(--navy);text-align:center;font-size:30px;letter-spacing:.5px;line-height:1.3}
.title-rule{width:86px;height:3px;background:var(--blue);margin:12px auto 0}
.btn{display:inline-block;background:var(--blue);color:var(--white);font-size:14px;border-radius:3px;padding:8px 18px;text-decoration:none;line-height:1.4}

/* header */
.site-header{position:absolute;top:0;left:0;width:1200px;height:82px;background:var(--white);display:flex;align-items:center;padding:0 88px;z-index:2}
.brand{display:flex;align-items:center;gap:12px}
.brand-mark{width:36px;height:36px;border-radius:50%;background:var(--blue)}
.brand-name{font-weight:700;color:var(--navy);font-size:26px;line-height:1}
.main-nav{margin-left:auto;display:flex;gap:44px;align-items:center;font-size:15px;color:var(--ink)}
.main-nav .btn{margin-left:10px;font-size:14px;padding:7px 20px}

/* hero */
.hero{position:absolute;top:82px;left:0;width:1200px;height:555px;clip-path:polygon(0 0,100% 0,100% 80%,0 100%);background:linear-gradient(120deg,#cfdcea 0%,#7ea6cf 35%,#2e6aa8 70%,#a9c2dd 100%)}
.hero-dots{position:absolute;top:516px;left:520px;display:flex;gap:8px}
.hero-dots span{width:16px;height:16px;border-radius:50%;border:2px solid var(--white);background:rgba(255,255,255,.3)}
.hero-dots span.on{background:var(--navy)}

/* welcome */
.welcome{position:absolute;top:700px;left:0;width:1200px;text-align:center}
.welcome p{width:920px;margin:20px auto 18px;font-size:12.5px;line-height:1.6;color:var(--ink)}

/* services */
.services{position:absolute;top:945px;left:0;width:1200px;height:1100px;background:var(--panel);border-top:1px solid #d4d7db}
.services .section-title{margin-top:100px}
.services .lead{width:700px;margin:14px auto 0;text-align:center;font-style:italic;color:var(--italic);font-size:14.5px;line-height:1.55}
.service-grid{position:absolute;top:288px;left:110px;width:980px;display:grid;grid-template-columns:repeat(3,1fr);row-gap:52px}
.service{text-align:center}
.service svg{display:block;margin:0 auto}
.service h3{margin-top:14px;font-size:20px;font-weight:600;color:var(--navy);text-transform:uppercase;line-height:1.4}
.service p{width:250px;margin:6px auto 0;font-size:14px;line-height:1.6;color:var(--ink)}

/* partners */
.partners{position:absolute;top:1905px;left:0;width:1200px;height:670px;clip-path:polygon(0 18%,100% 0,100% 90%,0 100%);background:linear-gradient(180deg,#0b5ea8 0%,#0a4a86 55%,#0d5a9d 100%)}
.partners .section-title{color:var(--white);position:absolute;top:150px;left:0;width:1200px;font-size:26px}
.partners .title-rule{position:absolute;top:196px;left:557px;background:var(--white);margin:0}
.partners .lead{position:absolute;top:205px;left:140px;width:920px;text-align:center;color:var(--white);font-size:17px;line-height:1.55}
.partner-grid{position:absolute;top:290px;left:89px;display:grid;grid-template-columns:repeat(5,182px);gap:27px 27px}
.partner{height:96px;background:var(--white);display:flex;align-items:center;justify-content:center}
.partner span{display:block;width:54px;height:54px;background:#3b3f45}
.partner span.round{border-radius:50%}
.partner-dots{position:absolute;top:552px;left:554px;display:flex;gap:8px}
.partner-dots span{width:16px;height:16px;border-radius:50%;border:2px solid var(--white)}
.partner-dots span.on{background:var(--white)}

/* blog */
.blog{position:absolute;top:2600px;left:0;width:1200px}
.blog .section-title{font-size:26px;margin-top:20px}
.blog-grid{position:absolute;top:107px;left:87px;display:grid;grid-template-columns:repeat(3,325px);gap:25px}
.post h3{font-size:18px;font-weight:600;color:var(--ink)}
.post-media{margin-top:12px;height:205px;border:2px solid #d9dde2}
.post p{margin-top:22px;font-size:12.5px;line-height:1.75;color:var(--muted)}
.post .more{display:block;margin-top:16px;font-size:13px;color:var(--ink)}

/* testimonials */
.testimonials{position:absolute;top:3190px;left:0;width:1200px;height:470px;clip-path:polygon(0 0,100% 8%,100% 100%,0 100%);background:linear-gradient(180deg,#0c6bbf 0%,#0a5aa3 60%,#0a4f91 100%)}
.testimonials .section-title{position:absolute;top:140px;left:0;width:1200px;color:var(--white);font-size:26px;font-weight:500}
.testimonials .title-rule{position:absolute;top:186px;left:557px;background:var(--white);margin:0}
.avatar{position:absolute;top:226px;left:120px;width:130px;height:130px;border-radius:50%;border:4px solid var(--white);background:linear-gradient(160deg,#c69b7a,#6d4a35)}
.quote{position:absolute;top:222px;left:338px;width:742px;padding-left:22px;border-left:1px solid rgba(255,255,255,.5);color:var(--white);font-size:15.5px;line-height:1.75}
.quote cite{display:block;margin-top:12px;font-style:normal;font-size:17px}
.quote-arrows{position:absolute;top:388px;left:362px;display:flex;gap:4px}
.quote-arrows span{width:22px;height:22px;display:flex;align-items:center;justify-content:center}

/* footer */
.site-footer{position:absolute;top:3660px;left:0;width:1200px;height:403px;background:var(--footer);color:var(--white)}
.footer-col{position:absolute;top:46px}
.footer-col h4{font-size:17px;font-weight:500;text-transform:uppercase;padding-bottom:8px;border-bottom:1px solid var(--footer-line);width:250px}
.contact-list{list-style:none;margin-top:26px;font-size:13px;line-height:1.6}
.contact-list li{display:flex;gap:18px;margin-bottom:14px}
.contact-list svg{flex:none;margin-top:3px}
.socials{display:flex;gap:14px;margin-top:8px}
.socials span{width:20px;height:20px;border-radius:50%;background:var(--white)}
.field{width:238px;height:40px;border:1px solid #5b5f66;margin-top:14px;font-size:13px;color:#b9bdc3;padding:9px 12px}
.field.area{height:62px}
.send{margin-top:14px;display:inline-block;background:var(--blue-bright);color:var(--white);font-size:13px;padding:6px 26px}
.newsletter p{margin-top:24px;width:230px;font-size:13px;line-height:1.55}
.subscribe{margin-top:26px;display:flex;width:270px;height:48px}
.subscribe .input{flex:1;background:var(--white);color:#6b7179;font-size:13px;padding:14px 14px}
.subscribe .go{width:58px;background:var(--blue-bright);display:flex;align-items:center;justify-content:center}
.footer-bar{position:absolute;top:352px;left:85px;width:1030px;border-top:1px solid var(--footer-line);padding-top:18px;display:flex;font-size:12.5px;color:#d7d9dc}
.footer-bar nav{display:flex;gap:42px}
.footer-bar .copy{margin-left:auto}
</style>
</head>
<body>

<header class="site-header">
  <div class="brand"><span class="brand-mark"></span><span class="brand-name">calderwen</span></div>
  <nav class="main-nav">
    <span>Home</span><span>Partners</span><span>Services</span><span>Downloads</span><span>Events</span><span>Contact</span>
    <span class="btn">Request a quote</span>
  </nav>
</header>

<section class="hero" role="img" aria-label="Businessman touching a glowing big data interface with charts and a world map"></section>
<div class="hero-dots abs"><span></span><span class="on"></span><span></span><span></span></div>

<section class="welcome">
  <h1 class="section-title" style="font-size:34px">Welcome to Calderwen Consulting</h1>
  <div class="title-rule"></div>
  <p>Lorem Ipsum is simply dummy text of the printing and typesetting industry. Lorem Ipsum has been the industry's standard dummy text ever since the 1500s, when an unknown printer took a galley of type and scrambled it to make a type specimen book. It has survived not only five centuries, but also the leap into electronic typesetting, remaining essentially unchanged. It was popularised in the 1960s with the release of Letraset sheets containing Lorem Ipsum passages, and more recently with desktop publishing software like Aldus PageMaker including versions of Lorem Ipsum.</p>
  <span class="btn">Read More &rsaquo;</span>
</section>

<section class="services">
  <h2 class="section-title">Our Services</h2>
  <div class="title-rule"></div>
  <p class="lead">Lorem Ipsum is simply dummy text of the printing and typesetting industry. Lorem Ipsum has been the industry's standard dummy text ever since the 1500s, when an unknown printer took a galley of type and scrambled it to make a type specimen book. It has survived not only five centuries</p>
  <div class="service-grid">
    <div class="service">
      <svg width="156" height="135" viewBox="0 0 196 170"><polygon points="49,3 147,3 194,85 147,167 49,167 2,85" fill="none" stroke="#2a4c7c" stroke-width="3"/><polygon points="53,10 143,10 186,85 143,160 53,160 10,85" fill="var(--hex)"/><circle cx="98" cy="85" r="38" fill="#3a5f94" role="img" aria-label="Database icon"/></svg>
      <h3>Data Warehousing</h3>
      <p>Lorem ipsum is simply dummy text of the printing and typesetting industry. Lorem Ipsum has been the industry's standard dummy text</p>
    </div>
    <div class="service">
      <svg width="156" height="135" viewBox="0 0 196 170"><polygon points="49,3 147,3 194,85 147,167 49,167 2,85" fill="none" stroke="#2a4c7c" stroke-width="3"/><polygon points="53,10 143,10 186,85 143,160 53,160 10,85" fill="var(--hex)"/><circle cx="98" cy="85" r="38" fill="#263a55" role="img" aria-label="Head with gears icon"/></svg>
      <h3>Business Intelligence</h3>
      <p>Lorem ipsum is simply dummy text of the printing and typesetting industry. Lorem Ipsum has been the industry's standard dummy text</p>
    </div>
    <div class="service">
      <svg width="156" height="135" viewBox="0 0 196 170"><polygon points="49,3 147,3 194,85 147,167 49,167 2,85" fill="none" stroke="#2a4c7c" stroke-width="3"/><polygon points="53,10 143,10 186,85 143,160 53,160 10,85" fill="var(--hex)"/><circle cx="98" cy="85" r="38" fill="#4f86c2" role="img" aria-label="Magnifier over chart icon"/></svg>
      <h3>Advanced Analytics</h3>
      <p>Lorem ipsum is simply dummy text of the printing and typesetting industry. Lorem Ipsum has been the industry's standard dummy text</p>
    </div>
    <div class="service">
      <svg width="156" height="135" viewBox="0 0 196 170"><polygon points="49,3 147,3 194,85 147,167 49,167 2,85" fill="none" stroke="#2a4c7c" stroke-width="3"/><polygon points="53,10 143,10 186,85 143,160 53,160 10,85" fill="var(--hex)"/><circle cx="98" cy="85" r="38" fill="#5b7ea8" role="img" aria-label="Database stack icon"/></svg>
      <h3>Big Data</h3>
      <p>Lorem ipsum is simply dummy text of the printing and typesetting industry. Lorem Ipsum has been the industry's standard dummy text</p>
    </div>
    <div class="service">
      <svg width="156" height="135" viewBox="0 0 196 170"><polygon points="49,3 147,3 194,85 147,167 49,167 2,85" fill="none" stroke="#2a4c7c" stroke-width="3"/><polygon points="53,10 143,10 186,85 143,160 53,160 10,85" fill="var(--hex)"/><circle cx="98" cy="85" r="38" fill="#6c7b8c" role="img" aria-label="Connected servers icon"/></svg>
      <h3>Data Integration</h3>
      <p>Lorem ipsum is simply dummy text of the printing and typesetting industry. Lorem Ipsum has been the industry's standard dummy text</p>
    </div>
    <div class="service">
      <svg width="156" height="135" viewBox="0 0 196 170"><polygon points="49,3 147,3 194,85 147,167 49,167 2,85" fill="none" stroke="#2a4c7c" stroke-width="3"/><polygon points="53,10 143,10 186,85 143,160 53,160 10,85" fill="var(--hex)"/><circle cx="98" cy="85" r="38" fill="#6fb3e0" role="img" aria-label="Cloud icon"/></svg>
      <h3>Cloud</h3>
      <p>Lorem ipsum is simply dummy text of the printing and typesetting industry. Lorem Ipsum has been the industry's standard dummy text</p>
    </div>
  </div>
</section>

<section class="partners">
  <h2 class="section-title">Our Strategic Partners</h2>
  <div class="title-rule"></div>
  <p class="lead">Lorem Ipsum is simply dummy text of the printing and typesetting industry. Lorem Ipsum has been the industry's standard dummy text ever since the 1500s.</p>
  <div class="partner-grid">
    <div class="partner"><span></span></div>
    <div class="partner"><span class="round"></span></div>
    <div class="partner"><span></span></div>
    <div class="partner"><span></span></div>
    <div class="partner"><span class="round"></span></div>
    <div class="partner"><span class="round"></span></div>
    <div class="partner"><span></span></div>
    <div class="partner"><span class="round"></span></div>
    <div class="partner"><span></span></div>
    <div class="partner"><span></span></div>
  </div>
  <div class="partner-dots"><span class="on"></span><span></span><span></span></div>
</section>

<section class="blog">
  <h2 class="section-title">Our Blog</h2>
  <div class="title-rule"></div>
  <div class="blog-grid">
    <article class="post">
      <h3>Lorem Ipsum is simply dummy</h3>
      <div class="post-media" role="img" aria-label="Businessman pressing a big data screen" style="background:linear-gradient(135deg,#9dbbd9,#2f5e96 60%,#1c3a63)"></div>
      <p>Sed ut perspiciatis unde omnis iste natus error sit voluptatem accusantium doloremque laudantium, totam rem aperiam, eaque ipsa quae ab illo inventore veritatis et quasi architecto beatae vitae dicta sunt explicabo. Nemo enim ipsam voluptatem...</p>
      <span class="more">Read More &rsaquo;</span>
    </article>
    <article class="post">
      <h3>Lorem Ipsum is simply dummy</h3>
      <div class="post-media" role="img" aria-label="Hand drawing an analytics chart on glass" style="background:linear-gradient(135deg,#e6eaef,#9aa8b8 55%,#5f6f82)"></div>
      <p>Sed ut perspiciatis unde omnis iste natus error sit voluptatem accusantium doloremque laudantium, totam rem aperiam, eaque ipsa quae ab illo inventore veritatis et quasi architecto beatae vitae dicta sunt explicabo. Nemo enim ipsam voluptatem...</p>
      <span class="more">Read More &rsaquo;</span>
    </article>
    <article class="post">
      <h3>Lorem Ipsum is simply dummy</h3>
      <div class="post-media" role="img" aria-label="Person using a tablet with data overlays" style="background:linear-gradient(135deg,#1a3e70,#2f6fb2 55%,#0f2747)"></div>
      <p>Sed ut perspiciatis unde omnis iste natus error sit voluptatem accusantium doloremque laudantium, totam rem aperiam, eaque ipsa quae ab illo inventore veritatis et quasi architecto beatae vitae dicta sunt explicabo. Nemo enim ipsam voluptatem...</p>
      <span class="more">Read More &rsaquo;</span>
    </article>
  </div>
</section>

<section class="testimonials">
  <h2 class="section-title">What People Say About Us</h2>
  <div class="title-rule"></div>
  <div class="avatar" role="img" aria-label="Portrait of a client"></div>
  <blockquote class="quote">"Lorem Ipsum is simply dummy text of the printing and typesetting industry. Lorem Ipsum has been the industry's standard dummy text ever since the 1500s, when an unknown printer took a galley of type and scrambled it to make a type specimen book. It has survived not only five"
    <cite>- Ilse Marrow</cite>
  </blockquote>
  <div class="quote-arrows">
    <span style="background:#3aa0e6"><svg width="8" height="10" viewBox="0 0 8 10"><path d="M6 1 2 5l4 4" stroke="#fff" stroke-width="2" fill="none"/></svg></span>
    <span style="background:#3c4655"><svg width="8" height="10" viewBox="0 0 8 10"><path d="M2 1l4 4-4 4" stroke="#fff" stroke-width="2" fill="none"/></svg></span>
  </div>
</section>

<footer class="site-footer">
  <div class="footer-col" style="left:88px">
    <h4>Contact Us</h4>
    <ul class="contact-list">
      <li><svg width="12" height="16" viewBox="0 0 12 16"><path d="M6 0a6 6 0 0 0-6 6c0 4.5 6 10 6 10s6-5.5 6-10a6 6 0 0 0-6-6zm0 8.5A2.5 2.5 0 1 1 6 3.5a2.5 2.5 0 0 1 0 5z" fill="#fff"/></svg><span>418 Quarry Lane, Westbrook,<br>20417.</span></li>
      <li><svg width="12" height="14" viewBox="0 0 14 14"><path d="M3 0l3 3-2 2c1 2 3 4 5 5l2-2 3 3-2 3C6 14 0 8 0 3z" fill="#fff"/></svg><span>+0100 555 210</span></li>
      <li><svg width="14" height="11" viewBox="0 0 14 11"><rect width="14" height="11" rx="1" fill="#fff"/><path d="M0 1l7 5 7-5" stroke="#1f2124" stroke-width="1.4" fill="none"/></svg><span>info@calderwen.com</span></li>
    </ul>
    <div class="socials" aria-label="Social links"><span></span><span></span><span></span><span></span></div>
  </div>
  <div class="footer-col" style="left:463px">
    <h4>Send Us a Message</h4>
    <div class="field" style="margin-top:22px">Name</div>
    <div class="field">Email</div>
    <div class="field area">Message</div>
    <span class="send">SEND</span>
  </div>
  <div class="footer-col newsletter" style="left:845px">
    <h4 style="width:270px">Newsletter Subscribe</h4>
    <p>Subscribe to our newsletter and we will inform you about Latest News.</p>
    <div class="subscribe">
      <span class="input">Your email</span>
      <span class="go"><svg width="22" height="20" viewBox="0 0 22 20"><path d="M0 9 22 0 17 20 10 13 18 4 8 12z" fill="#fff"/></svg></span>
    </div>
  </div>
  <div class="footer-bar">
    <nav><span>Home</span><span>Partners</span><span>Services</span><span>Downloads</span><span>Events</span><span>Contact</span></nav>
    <span class="copy">Copyright &copy; 2017 Calderwen Consulting. All rights reserved.</span>
  </div>
</footer>

</body>
</html>
```